www.brightpathlingo.com -- International Language school needs a Wordpress Design

NOTE: This is for a complete WordPress website with coding (Design/develop)

We are a small, private English language school in business for 15 years. Our students come from around the world to study English at our centre in Toronto, Canada. Most of our students are in their 20's and come to study English with us for periods of 1-6 months before returning home to complete their post-secondary education or pursue their careers.

We are looking for a talented web designer to redevelop our sadly outdated website (www.brightpathlingo.com) to bring a fresh look with vastly increased functionality and web traffic.

Target Market(s)

-20s and 30s; mostly upper-middle class, educated
-from non-English speaking countries, but often have some English background
-looking to improve their English (mostly speaking) skills at our school like ours and experience living in a new country (like exchange students)

Industry/Entity Type

Education

Font styles to use
Sans Serif

Requirements
Must have
• - page listing our programs
- page with our fees and starting dates
- application form
- page showing why BRIGHTPATH (us)?
- page with accommodation options
* responsive design
Nice to have
• examples of other websites in our industry I like:

http://www.morvale-tutors.com/
http://www.dunfieldlanguages.com/en
http://en.plm.ca/
http://www.harrowgate-study.ac.uk/

```html
<!DOCTYPE html>
<html lang="en">
<head>
<meta charset="utf-8">
<title>BRIGHTPATH – Private English Language Learning School</title>
<link href="https://fonts.googleapis.com/css2?family=Raleway:wght@400;500;600;700&family=Open+Sans:wght@400;600&display=swap" rel="stylesheet">
<style>
:root{
  --green:#8cc63e;
  --green-dark:#7ab32e;
  --blue:#2b8ad1;
  --blue-overlay:rgba(35,132,205,.88);
  --orange:#f9a11b;
  --ink:#222;
  --text:#555;
  --muted:#777;
  --line:#e2e2e2;
  --band:#f1f1f1;
  --white:#fff;
}
*{box-sizing:border-box;margin:0;padding:0}
html,body{width:930px;height:1200px;overflow:hidden}
body{position:relative;background:var(--white);font-family:'Open Sans',Arial,sans-serif;color:var(--text)}
.sky{position:absolute;left:0;top:0;width:930px;height:330px;background:linear-gradient(180deg,#fff 0%,#f2f2f2 25%,#cfd2d4 70%,#c3c6c9 100%)}
.abs{position:absolute}

/* header */
.brand{left:117px;top:40px;display:flex;align-items:center;gap:8px}
.brand-dot{width:26px;height:26px;border-radius:50%;background:var(--blue)}
.brand-name{font-family:'Raleway',Arial,sans-serif;font-weight:700;font-size:26px;color:var(--ink);letter-spacing:.5px}
.lang{left:741px;top:29px;width:67px;height:19px;border:1px solid #ccc;background:#fff;font-size:8px;display:flex;align-items:center;gap:4px;padding-left:7px;color:#333}
.lang-flag{width:12px;height:8px;background:#2a4a9a}
.contact{right:118px;top:58px;text-align:right;font-size:7.5px;line-height:14px;color:#444}
.contact strong{font-weight:600;font-size:9px}

/* nav */
.nav{left:117px;top:111px;width:697px;height:33px;background:linear-gradient(180deg,#9fd14a,var(--green-dark));display:flex;align-items:center;padding-left:25px;gap:23px}
.nav a{font-family:'Raleway',Arial,sans-serif;font-weight:500;font-size:11px;color:#fff;text-decoration:none}

/* hero */
.hero{left:117px;top:144px;width:697px;height:296px;background:linear-gradient(135deg,#6b4a36 0%,#a07a5c 35%,#5a3e2e 65%,#3a2a22 100%)}
.hero-tag{left:117px;top:266px;width:271px;height:76px;background:var(--blue-overlay);padding:13px 0 0 24px;color:#fff;font-family:'Raleway',Arial,sans-serif}
.hero-tag h1{font-weight:500;font-size:23px;line-height:26px;letter-spacing:.3px}
.hero-tag p{font-size:16px;line-height:20px}
.dots{left:442px;top:418px;display:flex;gap:3px}
.dots i{width:11px;height:11px;border-radius:50%;background:#fff}
.dots i.on{background:#111}

/* features */
.features{left:117px;top:440px;width:697px;height:114px;display:flex;border:1px solid var(--line);border-top:0;background:linear-gradient(180deg,#fff 70%,#f4f4f4)}
.feature{flex:1;border-right:1px solid var(--line);text-align:center;padding-top:30px}
.feature:last-child{border-right:0}
.feature svg{width:26px;height:26px;display:block;margin:0 auto 10px}
.feature h3{font-family:'Raleway',Arial,sans-serif;font-weight:500;font-size:12px;color:var(--blue)}
.feature p{font-size:7px;color:#555;margin-top:4px}

/* intro */
.intro{left:150px;top:586px;width:632px;text-align:center}
.intro h2{font-family:'Raleway',Arial,sans-serif;font-weight:400;font-size:20px;color:var(--ink)}
.intro p{font-size:8px;line-height:14.5px;color:#444;margin-top:10px}

/* tiles */
.tile{top:690px;width:227px;height:160px}
.tile-img{height:112px}
.tile-cap{height:48px;padding:9px 0 0 16px;color:#fff}
.tile-cap h3{font-family:'Raleway',Arial,sans-serif;font-weight:500;font-size:14px}
.tile-cap p{font-family:'Raleway',Arial,sans-serif;font-size:9px;margin-top:2px;opacity:.95}

/* programs band */
.band{left:0;top:890px;width:930px;height:232px;background:var(--band);border-top:1px solid #ddd;border-bottom:1px solid #ddd}
.section-title{font-family:'Raleway',Arial,sans-serif;font-weight:400;font-size:16px;color:var(--ink)}
.program{top:942px;width:147px;height:150px;background:#fff;border:1px solid var(--line)}
.program-img{height:78px}
.program h4{font-family:'Raleway',Arial,sans-serif;font-weight:400;font-size:9.5px;line-height:12px;color:var(--green-dark);margin:10px 0 0 11px}
.program p{font-size:7px;line-height:11.5px;color:#666;margin:5px 10px 0 11px}
.video{left:603px;top:942px;width:210px;height:143px;background:linear-gradient(135deg,#8a6a52,#c7a88a 50%,#6a5444)}
.play{left:694px;top:998px}

/* footer */
.foot-links{left:118px;top:1148px;font-family:'Raleway',Arial,sans-serif;font-size:8.5px;color:#333}
.foot-links span{color:#555;margin:0 3px}
.copy{left:118px;top:1167px;font-size:7.5px;color:#444}
.partners{left:508px;top:1146px;display:flex;align-items:center;gap:16px}
.partners i{display:block;background:#c9d3de}
</style>
</head>
<body>
<div class="sky abs"></div>

<header>
  <div class="brand abs"><span class="brand-dot"></span><span class="brand-name">BRIGHTPATH</span></div>
  <div class="lang abs"><span class="lang-flag"></span>English
    <svg width="7" height="5" viewBox="0 0 7 5" style="margin-left:4px"><path d="M0 0h7L3.5 5z" fill="#444"/></svg></div>
  <div class="contact abs">418 Harbourview Avenue, Suite 210, Toronto,<br>Ontario, M5V 3K2 Canada<br><strong>Phone number: +1-416-555-0182</strong></div>
</header>

<nav class="nav abs">
  <a href="#">Home</a><a href="#">Our School</a><a href="#">Programs</a><a href="#">Fees &amp; Dates</a><a href="#">Accommodation</a><a href="#">After Class</a><a href="#">Agent</a><a href="#">Contact</a>
</nav>

<div class="hero abs" role="img" aria-label="Students studying together around a classroom table"></div>
<div class="hero-tag abs"><h1>PRIVATE ENGLISH</h1><p>Language Learning school</p></div>
<div class="dots abs"><i class="on"></i><i></i><i></i><i></i></div>

<section class="features abs">
  <div class="feature">
    <svg viewBox="0 0 26 26"><g fill="var(--blue)"><circle cx="13" cy="8" r="5"/><circle cx="5" cy="10" r="3.5"/><circle cx="21" cy="10" r="3.5"/><path d="M5 24c0-6 3.5-9 8-9s8 3 8 9z"/><path d="M0 22c0-4 2-6 5-6s3 1 3 1-2 2-2 5z"/><path d="M26 22c0-4-2-6-5-6s-3 1-3 1 2 2 2 5z"/></g></svg>
    <h3>Meet Our Students</h3><p>Lorem ipsum dolor sit amet conse</p></div>
  <div class="feature">
    <svg viewBox="0 0 26 26"><g fill="none" stroke="var(--blue)" stroke-width="2.2"><path d="M16 5H4v17h17V12"/><path d="M22 2l3 3-11 11-4 1 1-4z"/></g></svg>
    <h3>Admissions</h3><p>Praesent elementum elit at tellus</p></div>
  <div class="feature">
    <svg viewBox="0 0 26 26"><circle cx="13" cy="13" r="12.5" fill="var(--blue)"/><path d="M9 10a4 4 0 1 1 5.5 3.7c-1 .5-1.5 1.2-1.5 2.3v1" fill="none" stroke="#fff" stroke-width="2.6"/><circle cx="13" cy="20.5" r="1.6" fill="#fff"/></svg>
    <h3>Got a Question?</h3><p>Lorem ipsum dolor sit amet consect</p></div>
  <div class="feature">
    <svg viewBox="0 0 26 26"><g fill="var(--blue)"><path d="M13 5L0 11l13 6 13-6z"/><path d="M6 14v5c0 2 3 4 7 4s7-2 7-4v-5l-7 3z"/><rect x="23" y="11" width="1.6" height="8"/></g></svg>
    <h3>Our Courses</h3><p>Praesent elementum elit at tellus</p></div>
  <div class="feature">
    <svg viewBox="0 0 26 26"><circle cx="13" cy="13" r="12.5" fill="var(--blue)"/><path d="M7 13.5l4 4 8-8" fill="none" stroke="#fff" stroke-width="3"/></svg>
    <h3>Apply Now</h3><p>Lorem ipsum dolor sit amet consect</p></div>
</section>

<section class="intro abs">
  <h2>Mauris vel lacus vitae felis vestibulum volutpat est nunc</h2>
  <p>cligula augue bibendum accumsan vestibulum ut commodo a mi Morbi ornare gravida elit Integer congue augue et malesuada iaculis ipsum dui aliquet felis at cursus magna nisl nec elit Praesent elementum elit at tellus nec ultricies sit amet porttitor mattis enim In massa libero interdum nec interdum vel blandit sed nulla In ullamcorper est eget tempor cursus neque mi consectetuer mi a ultricies massa est sed nisl Class apte</p>
</section>

<article class="tile abs" style="left:117px">
  <div class="tile-img" role="img" aria-label="Students in discussion at a classroom table" style="background:linear-gradient(135deg,#d9cfa8,#a88f6a 60%,#6d5a48)"></div>
  <div class="tile-cap" style="background:var(--blue)"><h3>Fees &amp; Dates</h3><p>Curabitur iaculis tempus eros Curabitur vel</p></div>
</article>
<article class="tile abs" style="left:351px">
  <div class="tile-img" role="img" aria-label="Two students chatting outdoors" style="background:linear-gradient(135deg,#5d8a2c,#b89a7c 50%,#2a2420)"></div>
  <div class="tile-cap" style="background:var(--orange)"><h3>Recent News</h3><p>Curabitur iaculis tempus eros Curabitur vel</p></div>
</article>
<article class="tile abs" style="left:586px">
  <div class="tile-img" role="img" aria-label="Group of students on a canoe trip wearing life jackets" style="background:linear-gradient(135deg,#4a6a8a,#c24a3a 50%,#2c4c7a)"></div>
  <div class="tile-cap" style="background:var(--green)"><h3>Photo Gallery</h3><p>Curabitur iaculis tempus eros Curabitur vel</p></div>
</article>

<div class="band abs"></div>
<h2 class="section-title abs" style="left:114px;top:918px">Our Programs</h2>
<h2 class="section-title abs" style="left:599px;top:917px">Watch Our Video</h2>

<article class="program abs" style="left:117px">
  <div class="program-img" role="img" aria-label="Students working on exercises" style="background:linear-gradient(135deg,#cfc6b8,#7d6e62)"></div>
  <h4>Full-Time Programs<br>Intensive Focus</h4>
  <p>Class aptent taciti sociosqu ad litora torquent per conubia nostra</p>
</article>
<article class="program abs" style="left:274px">
  <div class="program-img" role="img" aria-label="Host family in their kitchen" style="background:linear-gradient(135deg,#d8dadc,#5a6e8a 60%,#2a3a5a)"></div>
  <h4>Junior Programs<br>Parent &amp; Child</h4>
  <p>Class aptent taciti sociosqu ad litora torquent per conubia nost</p>
</article>
<article class="program abs" style="left:431px">
  <div class="program-img" role="img" aria-label="Smiling university students" style="background:linear-gradient(135deg,#5a4436,#c9a388 55%,#ece8e4)"></div>
  <h4>Special Programs<br>University Bridge</h4>
  <p>Class aptent taciti sociosqu ad litora torquent per conubia nost.</p>
</article>

<div class="video abs" role="img" aria-label="Video still of students writing at a table"></div>
<svg class="play abs" width="28" height="28" viewBox="0 0 28 28"><circle cx="14" cy="14" r="14" fill="#fff"/><path d="M11 8l9 6-9 6z" fill="#111"/></svg>

<footer>
  <div class="foot-links abs">Home<span>|</span>Our School<span>|</span>Programs<span>|</span>Fees &amp; Dates<span>|</span>Accommodation<span>|</span>After Class<span>|</span>Agent</div>
  <div class="copy abs">© 2015 Company Name&nbsp; All right reserved&nbsp; Term of Use</div>
  <div class="partners abs" aria-label="Accreditation partners">
    <i style="width:52px;height:22px"></i>
    <i style="width:64px;height:22px"></i>
    <i style="width:46px;height:22px"></i>
    <i style="width:24px;height:24px;border-radius:50%"></i>
    <i style="width:62px;height:22px"></i>
  </div>
</footer>
</body>
</html>
```